NEW Modern Sleek Business Card for VR Language Startup

Our startup is using VR to lead the next wave of world language education. We need a two-sided business card that introduces the larger organization (Brightloom Language Inc) and our contact info on one side and shows the product, Glimwoorld, on the other side.

Side 1 (contact info)= Brightloom Logo and Contact info (name, title, phone, email)

Side 2 (product)= Glimworld logo, text, and website
Text= Culturally Immersive Language Learning Games
Website= www.glimworld-play.com

Target Market(s)

Education, Technology

Contact Information for Business Card

Contact info will be updated upon approval of the design. For now, put this as a placeholder.

Perry Dunmore
Founder & CEO
pdunmore@quillpost-mail.net
(555)-014-2286

Font styles to use
Other font styles liked:
• Gibson and Century Gothic are the brand fonts

Requirements
Nice to have
• I would love to see cohesion between the design and colors of the two logos. I have attached a few business card designs that I like, so you can get a feel for my preferred style.

```html
<!DOCTYPE html>
<html lang="en">
<head>
<meta charset="utf-8">
<title>Glimworld / Brightloom Language — Business Card</title>
<link href="https://fonts.googleapis.com/css2?family=Montserrat:wght@700&family=Questrial&display=swap" rel="stylesheet">
<style>
  :root {
    --page: #e4e4e6;
    --card-dark-a: #060606;
    --card-dark-b: #2b2b2b;
    --ink: #1a1a1a;
    --muted: #5b5b5b;
    --tagline: #555555;
    --violet: #6a58ff;
    --sky: #3fa3f2;
    --accent-red: #e5283a;
    --white: #ffffff;
  }
  * { box-sizing: border-box; margin: 0; padding: 0; }
  html, body { width: 1200px; height: 1200px; overflow: hidden; }
  body {
    background: var(--page);
    font-family: "Questrial", "Century Gothic", sans-serif;
    position: relative;
  }
  .card {
    position: absolute;
    left: 150px;
    width: 900px;
    height: 514px;
    border-radius: 34px;
    overflow: hidden;
    box-shadow: 0 18px 40px rgba(0,0,0,.18);
  }

  /* Product side */
  .card--product {
    top: 66px;
    background: linear-gradient(120deg, var(--card-dark-a) 30%, var(--card-dark-b) 100%);
    text-align: center;
  }
  .product-mark {
    position: absolute;
    left: 50%;
    top: 70px;
    width: 150px;
    height: 150px;
    margin-left: -75px;
    border-radius: 50%;
    background: var(--sky);
  }
  .product-name {
    position: absolute;
    left: 0; right: 0;
    top: 232px;
    font-size: 86px;
    line-height: 1;
    color: var(--muted);
    letter-spacing: 1px;
  }
  .product-tagline {
    position: absolute;
    left: 0; right: 0;
    top: 340px;
    font-size: 22px;
    color: var(--tagline);
    letter-spacing: 1.5px;
  }
  .product-site {
    position: absolute;
    left: 0; right: 0;
    top: 420px;
    font-size: 22px;
    font-weight: 700;
    font-family: "Montserrat", sans-serif;
    color: var(--violet);
    letter-spacing: .5px;
  }

  /* Contact side */
  .card--contact {
    top: 620px;
    background: var(--white);
  }
  .brand-band {
    position: absolute;
    top: 0; right: 0; bottom: 0;
    width: 245px;
    background: linear-gradient(160deg, var(--card-dark-a), var(--card-dark-b));
  }
  .brand-lockup {
    position: absolute;
    left: 50%;
    top: 190px;
    transform: translate(-50%, -50%) rotate(-90deg);
    white-space: nowrap;
    color: var(--white);
    text-transform: uppercase;
    text-align: left;
    line-height: 1.1;
  }
  .brand-name {
    display: block;
    font-size: 36px;
    letter-spacing: 4px;
  }
  .brand-sub {
    display: block;
    font-size: 22px;
    letter-spacing: 9px;
    margin-top: 4px;
  }
  .brand-mark {
    position: absolute;
    left: 50%;
    bottom: 40px;
    width: 72px;
    height: 72px;
    margin-left: -36px;
    border-radius: 50%;
    background: var(--violet);
  }
  .contact {
    position: absolute;
    left: 60px;
    bottom: 70px;
    color: var(--ink);
  }
  .contact-name {
    font-family: "Montserrat", sans-serif;
    font-weight: 700;
    font-size: 34px;
    letter-spacing: .5px;
    text-transform: uppercase;
  }
  .contact-title {
    font-size: 22px;
    margin-left: 12px;
    font-family: "Questrial", sans-serif;
    font-weight: 400;
    text-transform: none;
    letter-spacing: 0;
  }
  .contact-lines {
    display: flex;
    gap: 30px;
    margin-top: 14px;
    font-size: 20px;
  }
  .contact-item { display: flex; align-items: center; gap: 8px; }
  .contact-item svg { width: 20px; height: 20px; fill: var(--accent-red); }
</style>
</head>
<body>
  <section class="card card--product" aria-label="Product side">
    <div class="product-mark"></div>
    <div class="product-name">Glimworld</div>
    <div class="product-tagline">Culturally Immersive Language Learning Games</div>
    <div class="product-site">www.glimworld-play.com</div>
  </section>

  <section class="card card--contact" aria-label="Contact side">
    <div class="contact">
      <div class="contact-name">Perry Dunmore<span class="contact-title">Founder &amp; CEO</span></div>
      <div class="contact-lines">
        <span class="contact-item">
          <svg viewBox="0 0 24 24" aria-hidden="true"><path d="M6.6 10.8a15.1 15.1 0 0 0 6.6 6.6l2.2-2.2a1 1 0 0 1 1-.25 11.4 11.4 0 0 0 3.6.57 1 1 0 0 1 1 1V20a1 1 0 0 1-1 1A17 17 0 0 1 3 4a1 1 0 0 1 1-1h3.5a1 1 0 0 1 1 1c0 1.25.2 2.45.57 3.6a1 1 0 0 1-.25 1z"/></svg>
          (555)-014-2286
        </span>
        <span class="contact-item">
          <svg viewBox="0 0 24 24" aria-hidden="true"><path d="M3 5h18a1 1 0 0 1 1 1v12a1 1 0 0 1-1 1H3a1 1 0 0 1-1-1V6a1 1 0 0 1 1-1zm9 7.2L4 7.3V8l8 5 8-5v-.7z"/></svg>
          pdunmore@quillpost-mail.net
        </span>
      </div>
    </div>
    <div class="brand-band">
      <div class="brand-lockup">
        <span class="brand-name">Brightloom</span>
        <span class="brand-sub">Language</span>
      </div>
      <div class="brand-mark"></div>
    </div>
  </section>
</body>
</html>
```